Vitamin B12 Liquid Drops Label

hi, i need a label designed for my vitamin b12 drops that i am going to be selling on shopzello. the label needs to quickly capture the attention of a buyer as he or she is scrolling through the thumbnail search results on shopzello.com my brand is called nralo. i already have an example brand logo i will be using, however, i need help designing the rest of the label. attached are some examples of labels i like for other supplements.some of these examples are pink. i do not want pink. please go for a blue/green color scheme. THE DESIGN MUST BE BOLD

Target Market(s)

adults ages 30 - 64

Font styles to use
Sans Serif

Colors
0455a3
cedeed
3176b5
85acd3
cfdeed
9bcb3b
abd037
cadf82
00a990

Requirements
Must have
• - bold design
• - somewhat gender-neutral color scheme because this will be used equally by men and women
• - B12 MUST be very prominent and visible on the label
Should not have
• - it should not be "crunchy" looking

```html
<!DOCTYPE html>
<html lang="en">
<head>
<meta charset="utf-8">
<title>nralo Vitamin B12 Drops – Packaging</title>
<link rel="stylesheet" href="https://fonts.googleapis.com/css2?family=Fira+Sans:wght@700;800&display=swap">
<style>
  :root {
    --stage: #033d75;
    --navy: #0455a3;
    --mid-blue: #3176b5;
    --sky: #85acd3;
    --mist: #cedeed;
    --green: #9bcb3b;
    --lime: #abd037;
    --pale-lime: #cadf82;
    --teal: #00a990;
  }
  * { margin: 0; padding: 0; box-sizing: border-box; }
  html, body { width: 1200px; height: 800px; overflow: hidden; }
  body {
    background: var(--stage);
    font-family: "Fira Sans", Arial, sans-serif;
  }
  .artboard { position: relative; width: 1200px; height: 800px; }
  .box-front {
    position: absolute;
    left: 412px; top: 128px;
    width: 208px; height: 432px;
    display: block;
  }
  .drop-label {
    position: absolute;
    left: 659px; top: 356px;
    width: 136px; height: 168px;
    display: block;
  }
  .wordmark { font-weight: 800; }
  .product-name { font-weight: 800; }
  .ingredient { font-weight: 700; }
</style>
</head>
<body>
<main class="artboard">

  <!-- Carton front panel -->
  <svg class="box-front" viewBox="0 0 260 540" aria-label="nralo Vitamin B12 carton front">
    <rect class="carton-face" x="0" y="0" width="260" height="540" fill="var(--green)"/>
    <rect class="carton-lid" x="0" y="0" width="260" height="34" fill="var(--sky)"/>
    <polygon class="accent-band" points="0,372 100,332 260,440 260,532 0,480" fill="var(--teal)"/>
    <polygon class="title-band" points="0,296 260,186 260,270 0,380" fill="var(--mid-blue)"/>
    <text class="wordmark" x="16" y="248" font-size="60" fill="var(--navy)"
          textLength="222" lengthAdjust="spacingAndGlyphs"
          transform="rotate(-22 16 248)">NRALO</text>
    <text class="product-name" x="16" y="352" font-size="36" fill="var(--pale-lime)"
          textLength="244" lengthAdjust="spacingAndGlyphs"
          transform="rotate(-22 16 352)">VITAMIN B12</text>
  </svg>

  <!-- Dropper bottle label -->
  <svg class="drop-label" viewBox="0 0 170 210" aria-label="nralo Vitamin B12 dropper label">
    <rect class="label-base" x="0" y="0" width="170" height="210" fill="var(--navy)"/>
    <polygon class="label-panel" points="0,0 170,0 122,110 0,110" fill="var(--lime)"/>
    <text class="product-name" x="5" y="108" font-size="19" fill="var(--navy)"
          textLength="114" lengthAdjust="spacingAndGlyphs">VITAMIN B12</text>
    <text class="ingredient" x="9" y="124" font-size="6" fill="var(--pale-lime)"
          textLength="108" lengthAdjust="spacing">METHYLCOBAMALIN</text>
    <text class="wordmark" x="98" y="196" font-size="17" fill="var(--lime)"
          textLength="64" lengthAdjust="spacingAndGlyphs">NRALO</text>
  </svg>

</main>
</body>
</html>
```